Brintel Works - Fast, Efficient and Gas Mainteance for Domestic, Commercial and Industrial clients

We are in the process of purchasing a new business and would like to get a new logo and business card.
Business is a gas maintenance business that also does new gas installations.
Has been established since 1988.
Services include:
Install all types of gas appliances & equipment inc. hot water units
Maintain / repair / replace all types of gas appliances & equipment

Target Market(s)

Domestic, Commercial and Industrial clients

Industry/Entity Type

Business

Contact Information for Business Card

admin@brintelworks.com.au
07 3918 4726
Brintel Works PTY LTD

Logo Text

Gas Fitting & Plumbing Maintenance Specialists

Font styles to use
Sans Serif

Requirements
Must have
• Logo
• Business name, contact number, email address, web address
• Domestic | Commercial | Industrial Est Since 1988
Nice to have
• Possibly a black card with a flame logo to one side
Should not have
• Spelling errors

```html
<!DOCTYPE html>
<html lang="en">
<head>
<meta charset="utf-8">
<title>Brintel Works – Business Card</title>
<link rel="stylesheet" href="https://fonts.googleapis.com/css2?family=Didact+Gothic&family=PT+Sans:wght@400&display=swap">
<style>
  :root {
    --backdrop: #9a9a98;
    --card-black: #0b0b0b;
    --card-black-soft: #1c1c1c;
    --logo-yellow: #f3d320;
    --flame-orange: #f08a1c;
    --flame-gold: #f8c040;
    --flame-red: #c2410c;
    --text-light: #f2f2f2;
    --rule: #3a3a3a;
    --icon-orange: #e8731c;
  }
  * { box-sizing: border-box; margin: 0; padding: 0; }
  html, body { width: 1200px; height: 900px; overflow: hidden; }
  body {
    background: var(--backdrop);
    font-family: "PT Sans", sans-serif;
    display: flex;
    flex-direction: column;
    align-items: center;
    justify-content: center;
    gap: 56px;
  }
  .card {
    width: 620px;
    height: 354px;
    position: relative;
    overflow: hidden;
    border-radius: 2px;
  }

  /* Front */
  .card-front { background: var(--card-black); }
  .card-front .brand {
    position: absolute;
    left: 52px;
    top: 40px;
    color: var(--text-light);
    font-family: "Didact Gothic", sans-serif;
  }
  .brand-name { font-size: 40px; line-height: 1; letter-spacing: 0.5px; }
  .brand-entity { font-size: 13px; letter-spacing: 3.2px; margin-top: 4px; }
  .flame-area {
    position: absolute;
    left: 0; right: 0; bottom: 0;
    height: 210px;
    background:
      radial-gradient(ellipse 60% 70% at 50% 100%, var(--flame-gold) 0%, var(--flame-orange) 35%, rgba(194,65,12,0.6) 60%, rgba(11,11,11,0) 85%),
      linear-gradient(to top, rgba(240,138,28,0.5), rgba(11,11,11,0));
  }

  /* Back */
  .card-back {
    background: radial-gradient(ellipse at 50% 25%, var(--card-black-soft), var(--card-black) 75%);
    color: var(--text-light);
  }
  .card-back .brand {
    position: absolute;
    top: 52px;
    left: 0; right: 0;
    text-align: center;
    color: var(--logo-yellow);
    font-family: "Didact Gothic", sans-serif;
  }
  .card-back .brand-name { font-size: 52px; }
  .card-back .brand-entity { font-size: 15px; letter-spacing: 3.6px; margin-top: 2px; }
  .divider {
    position: absolute;
    left: 40px; right: 40px;
    top: 172px;
    border-top: 1px solid var(--rule);
  }
  .address {
    position: absolute;
    left: 64px;
    top: 196px;
    font-size: 17px;
    line-height: 1.3;
  }
  .contact-list {
    position: absolute;
    left: 360px;
    top: 210px;
    list-style: none;
    font-size: 17px;
    line-height: 1.35;
  }
  .contact-list li { display: flex; align-items: center; gap: 10px; }
  .contact-list svg { width: 12px; height: 12px; flex: none; }
  .sectors {
    position: absolute;
    left: 64px;
    top: 282px;
    font-size: 18px;
  }
</style>
</head>
<body>

  <section class="card card-front">
    <div class="brand">
      <div class="brand-name">Brintel Works</div>
      <div class="brand-entity">PTY LTD</div>
    </div>
    <div class="flame-area" role="img" aria-label="Photograph of orange gas flames along the lower half of the card"></div>
  </section>

  <section class="card card-back">
    <div class="brand">
      <div class="brand-name">Brintel Works</div>
      <div class="brand-entity">PTY LTD</div>
    </div>
    <div class="divider"></div>
    <p class="address">12345, Address Goes Here<br>Country Name, 123456.</p>
    <ul class="contact-list">
      <li>
        <svg viewBox="0 0 12 12" aria-hidden="true"><path fill="var(--icon-orange)" d="M2.5 1l2 2.2-1 1.3a6 6 0 0 0 4 4l1.3-1 2.2 2-1.3 1.5C5 10.8 1.2 7 1 2.3z"/></svg>
        07 3918 4726
      </li>
      <li>
        <svg viewBox="0 0 12 12" aria-hidden="true"><rect x="0.5" y="2" width="11" height="8" fill="var(--icon-orange)"/><path d="M0.5 2l5.5 4.5L11.5 2" fill="none" stroke="#fff" stroke-width="1"/></svg>
        admin@brintelworks.com.au
      </li>
      <li>
        <svg viewBox="0 0 12 12" aria-hidden="true"><circle cx="6" cy="6" r="5.5" fill="var(--icon-orange)"/><path d="M0.5 6h11M6 0.5c-3 3-3 8 0 11M6 0.5c3 3 3 8 0 11" fill="none" stroke="#fff" stroke-width="0.8"/></svg>
        www.brintelworks.com.au
      </li>
    </ul>
    <p class="sectors">Domestic | Commercial | Industrial Est Since 1988</p>
  </section>

</body>
</html>
```